Cedarvale Ridge College

We are looking to update our current webpage at www.cedarvaleridge.ca. We would like to make it modern, fresh and appealing to students. We want to keep our logo the same with the logo colours blended in as the primary colours and focus. We are open to reconfiguring content as well.
Reason: Hi, In the next 3 days we will have narrowed our search to 3 designs and will make a choice before the final deadline...
College

```html
<!DOCTYPE html>
<html lang="en">
<head>
<meta charset="utf-8">
<title>Cedarvale Ridge College</title>
<link href="https://fonts.googleapis.com/css2?family=Open+Sans:wght@400;600;700&display=swap" rel="stylesheet">
<style>
:root{
  --teal:#1f8a72;
  --teal-dark:#176b58;
  --title-teal:#1b7e6c;
  --navy:#1f3c66;
  --navy-soft:#2d4d7a;
  --text:#555b61;
  --muted:#8b9096;
  --line:#d9dcdf;
  --grey-bg:#f1f2f3;
  --footer:#3b3b3c;
}
*{margin:0;padding:0;box-sizing:border-box}
html,body{width:1200px;height:2163px;overflow:hidden;background:#fff}
body{position:relative;font-family:"Open Sans",Arial,sans-serif;color:var(--text)}
h2,h3{font-weight:400}
.abs{position:absolute}

.brand{left:101px;top:30px;width:260px;color:var(--navy);font-weight:700;font-size:26px;line-height:26px;letter-spacing:.5px;text-transform:uppercase}
.tagline{right:99px;top:34px;font-size:21px;letter-spacing:.5px;color:var(--navy)}
.social{right:99px;top:86px;display:flex;gap:11px}
.social span{width:22px;height:22px;border-radius:2px}

.nav{left:0;top:141px;width:1200px;height:55px;background:var(--teal)}
.nav ul{position:absolute;left:101px;top:0;height:55px;display:flex;list-style:none}
.nav li{height:55px;line-height:55px;padding:0 13px;color:#fff;font-size:15px;border-right:1px solid rgba(255,255,255,.18)}
.nav li.active{background:var(--teal-dark)}

.hero{left:0;top:196px;width:1200px;height:522px;background:linear-gradient(135deg,#d9d6cf 0%,#b9b3a7 35%,#e9e6e0 60%,#8c93a0 100%)}
.slide-arrow{top:433px;width:40px;height:50px;background:rgba(40,40,40,.35);display:flex;align-items:center;justify-content:center}

.quick{left:101px;top:718px;width:1000px;height:82px;border-bottom:2px solid var(--line);display:flex}
.quick a{flex:1;display:flex;align-items:center;justify-content:center;gap:12px;color:var(--navy);font-size:21px;font-weight:600;text-decoration:none;position:relative}
.quick a+a::before{content:"";position:absolute;left:0;top:14px;height:46px;width:1px;background:var(--line)}

.section-title{font-size:27px;color:var(--title-teal)}
.video{left:101px;top:910px;width:281px;height:211px;background:linear-gradient(180deg,#4b4a46 0%,#8a7c62 55%,#5c6b4e 100%)}
.play{left:222px;top:996px;width:40px;height:40px;border-radius:50%;background:rgba(255,255,255,.85);border:2px solid #333}
.intro{left:401px;top:908px;width:410px;font-size:13.3px;line-height:23px}
.intro p+p{margin-top:9px}
.divider{left:835px;top:851px;width:1px;height:270px;background:var(--line)}
.links{left:858px;top:902px;list-style:none;font-size:14.5px;line-height:33.2px;color:#4a5056}
.links li::before{content:"• "}

.news-band{left:0;top:1194px;width:1200px;height:407px;background:var(--grey-bg)}
.news-title{left:101px;top:1226px;font-size:27px;color:var(--navy-soft)}
.more{left:1076px;top:1235px}
.cards{left:101px;top:1278px;display:flex;gap:25px}
.card{width:231px;height:283px;background:#fff;border:1px solid #e2e4e6}
.card .thumb{height:136px}
.card h3{margin:14px 14px 0;font-size:13px;line-height:19px;font-weight:600;color:#333}
.card p{margin:9px 14px 0;font-size:12px;line-height:17px;color:var(--muted)}
.card .meta{margin:16px 14px 0;display:flex;align-items:center;gap:12px;font-size:12px;color:#777}

.btn{top:1641px;height:72px;display:flex;align-items:center;justify-content:center;gap:10px;font-size:21px;text-transform:uppercase}
.btn.map{left:101px;width:499px;border:2px solid #6cc3b3;color:var(--teal)}
.btn.gallery{left:598px;width:502px;border:2px solid #6a7ea8;color:var(--navy)}

.map-area{left:0;top:1758px;width:1200px;height:287px;background:linear-gradient(90deg,#e6ebe0 0%,#dfe7d4 50%,#e8ece2 100%)}
.contact{left:100px;top:1794px;width:302px;height:188px;background:rgba(70,88,122,.88);border-radius:3px;color:#fff;font-size:14.5px;line-height:23px;padding:10px 17px;font-style:normal}
.contact .gap{margin-top:10px}
.contact b{font-weight:600}

.footer{left:0;top:2045px;width:1200px;height:118px;background:var(--footer);color:#e6e6e6;text-align:center;font-size:13.5px}
.footer .fnav{margin-top:30px}
.footer .fnav span{margin:0 9px}
.footer .copy{margin-top:12px}
</style>
</head>
<body>

<header>
  <div class="abs brand">Cedarvale<br>Ridge<br>College</div>
  <div class="abs tagline">learn. grow. lead</div>
  <div class="abs social">
    <span style="background:#3b5a9a"></span>
    <span style="background:#3fa9e0"></span>
    <span style="background:#d8332a"></span>
    <span style="background:#f08a2a"></span>
  </div>
</header>

<nav class="abs nav">
  <ul>
    <li class="active">Home</li><li>About Us</li><li>Contact Us</li><li>Consider Cedarvale</li><li>Current Students</li><li>Alumni</li><li>Supporters</li><li>News + Events</li><li>Cedarvale Park</li>
  </ul>
</nav>

<div class="abs hero" role="img" aria-label="Students reading together around a library table with an instructor"></div>
<div class="abs slide-arrow" style="left:0"><svg width="14" height="26"><path d="M12 2 L2 13 L12 24" stroke="#fff" stroke-width="2" fill="none"/></svg></div>
<div class="abs slide-arrow" style="right:0"><svg width="14" height="26"><path d="M2 2 L12 13 L2 24" stroke="#fff" stroke-width="2" fill="none"/></svg></div>

<div class="abs quick">
  <a><svg width="28" height="28" viewBox="0 0 28 28"><rect x="2" y="5" width="20" height="20" fill="none" stroke="var(--navy)" stroke-width="2.5"/><path d="M10 18 L24 4" stroke="var(--navy)" stroke-width="3"/></svg>Apply Today</a>
  <a><svg width="30" height="18" viewBox="0 0 30 18"><rect x="1" y="3" width="28" height="12" rx="2" fill="var(--navy)"/><rect x="6" y="6" width="18" height="6" fill="#fff"/></svg>Donate</a>
  <a><svg width="24" height="30" viewBox="0 0 24 30"><rect x="2" y="2" width="19" height="26" rx="2" fill="var(--navy)"/><rect x="5" y="22" width="16" height="3" fill="#fff"/></svg>Library</a>
  <a><svg width="30" height="30" viewBox="0 0 30 30"><circle cx="15" cy="15" r="14" fill="var(--navy)"/><rect x="13.5" y="13" width="3" height="10" fill="#fff"/><circle cx="15" cy="9" r="2" fill="#fff"/></svg>Text for Info</a>
</div>

<h2 class="abs section-title" style="left:101px;top:852px">Welcome to Cedarvale Ridge College</h2>
<div class="abs video" role="img" aria-label="Video still of a college basketball game in a gym"></div>
<div class="abs play"><svg width="36" height="36"><path d="M14 10 L26 18 L14 26 Z" fill="#222"/></svg></div>
<div class="abs intro">
  <p>Donec eget gravida ipsum. Curabitur quam nulla, aliquam et fermentum mattis, vehicula eu mauris. In elementum tortor sed turpis dapibus semper.</p>
  <p>Vestibulum elementum iaculis pulvinar. Donec pharetra pretium nisi, non suscipit neque volutpat ut. In hac habitasse platea dictumst. Fusce consectetur ut tellus at ullamcorper. Etiam vitae nibh laoreet, semper elit sit amet, scelerisque lectus. Nam hendrerit interdum luctus. Duis vulputate enim eget nisl pharetra luctus.</p>
</div>
<div class="abs divider"></div>
<h2 class="abs section-title" style="left:858px;top:852px">Useful Links</h2>
<ul class="abs links">
  <li>Download the full Catalogue</li>
  <li>Apply Today (Application Package)</li>
  <li>Information Request</li>
  <li>Browse our Programs</li>
  <li>Download Forms</li>
  <li>Admissions Information</li>
  <li>Campus Directory</li>
</ul>

<section class="abs news-band"></section>
<h2 class="abs news-title">News and Events</h2>
<svg class="abs more" width="22" height="22" viewBox="0 0 22 22"><circle cx="11" cy="11" r="9" fill="none" stroke="var(--navy)" stroke-width="2"/><path d="M6 11 H15 M11 7 L15 11 L11 15" stroke="var(--navy)" stroke-width="2" fill="none"/></svg>
<div class="abs cards">
  <article class="card"><div class="thumb" role="img" aria-label="Faculty member in graduation robes" style="background:linear-gradient(135deg,#3a2a22,#7a4a30)"></div><h3>"Not for Profit" Organizational Leadership.</h3><p>Etiam vitae nibh laoreet, semper elit sit amet, scelerisque lectus.</p><div class="meta">Nov 20, 2014 <svg width="12" height="10"><path d="M0 2 H4 L8 8 H12 M0 8 H4 L8 2 H12" stroke="#777" fill="none" stroke-width="1.5"/></svg><svg width="11" height="10"><path d="M0 0 H11 V7 H4 L1 10 V7 H0Z" fill="#777"/></svg></div></article>
  <article class="card"><div class="thumb" role="img" aria-label="Students in a classroom listening to a speaker" style="background:linear-gradient(135deg,#c9b58a,#5a4d3f)"></div><h3>"Not for Profit" Organizational Leadership.</h3><p>Etiam vitae nibh laoreet, semper elit sit amet, scelerisque lectus.</p><div class="meta">Nov 20, 2014 <svg width="12" height="10"><path d="M0 2 H4 L8 8 H12 M0 8 H4 L8 2 H12" stroke="#777" fill="none" stroke-width="1.5"/></svg><svg width="11" height="10"><path d="M0 0 H11 V7 H4 L1 10 V7 H0Z" fill="#777"/></svg></div></article>
  <article class="card"><div class="thumb" role="img" aria-label="Campus building with students walking outside" style="background:linear-gradient(180deg,#9aa6b0,#8a4a3c 60%,#6e6a62)"></div><h3>"Not for Profit" Organizational Leadership.</h3><p>Etiam vitae nibh laoreet, semper elit sit amet, scelerisque lectus.</p><div class="meta">Nov 20, 2014 <svg width="12" height="10"><path d="M0 2 H4 L8 8 H12 M0 8 H4 L8 2 H12" stroke="#777" fill="none" stroke-width="1.5"/></svg><svg width="11" height="10"><path d="M0 0 H11 V7 H4 L1 10 V7 H0Z" fill="#777"/></svg></div></article>
  <article class="card"><div class="thumb" role="img" aria-label="Student and visitor sharing a moment outdoors" style="background:linear-gradient(135deg,#b8a68e,#7a3a2e)"></div><h3>"Not for Profit" Organizational Leadership.</h3><p>Etiam vitae nibh laoreet, semper elit sit amet, scelerisque lectus.</p><div class="meta">Nov 20, 2014 <svg width="12" height="10"><path d="M0 2 H4 L8 8 H12 M0 8 H4 L8 2 H12" stroke="#777" fill="none" stroke-width="1.5"/></svg><svg width="11" height="10"><path d="M0 0 H11 V7 H4 L1 10 V7 H0Z" fill="#777"/></svg></div></article>
</div>

<a class="abs btn map"><svg width="24" height="24" viewBox="0 0 24 24"><rect x="1" y="1" width="22" height="22" fill="var(--teal)"/><rect x="5" y="5" width="5" height="5" fill="#fff"/><rect x="14" y="12" width="5" height="7" fill="#fff"/></svg>Campus Map</a>
<a class="abs btn gallery"><svg width="28" height="22" viewBox="0 0 28 22"><rect x="1" y="1" width="26" height="20" fill="none" stroke="var(--navy)" stroke-width="2"/><path d="M4 18 L11 10 L16 15 L19 12 L24 18Z" fill="var(--navy)"/><circle cx="20" cy="6" r="2" fill="var(--navy)"/></svg>Photo Gallery</a>

<div class="abs map-area" role="img" aria-label="Street map showing the college campus location"></div>
<svg class="abs" style="left:733px;top:1847px" width="18" height="26" viewBox="0 0 18 26"><path d="M9 25 C9 25 1 14 1 9 A8 8 0 0 1 17 9 C17 14 9 25 9 25Z" fill="#d33"/><circle cx="9" cy="9" r="3" fill="#8a1a1a"/></svg>
<address class="abs contact">
  Cedarvale Ridge College<br>
  4120 Larchmont Road<br>
  • PO Box 2210 • Ferndale • BC<br>
  • CANADA • V4K 2R9
  <div class="gap"><b>Call : &nbsp;1-800-555-0142 • (604) 555-0187</b></div>
  <div class="gap"><b>E-mail : info@cedarvaleridge.ca</b></div>
</address>

<footer class="abs footer">
  <div class="fnav">Home<span>|</span>About Us<span>|</span>Contact Us<span>|</span>Consider Cedarvale<span>|</span>Current Students<span>|</span>Alumni<span>|</span>Supporters<span>|</span>News + Events<span>|</span>Cedarvale Park</div>
  <div class="copy">Copyright &copy; 2014 &nbsp;Cedarvale Ridge College - All rights reserved</div>
</footer>

</body>
</html>
```